We are a local Communty Pharmacy wishing to promote and market a specialised Pharmaceutical Service

We would like a design that is professional and enticing ( according to the brief In attached files)
We wish to Market Compounding Pharmacy as a specialist side of our business.
We have the expertise a purpose built preparation laboratory.
The main purpose is an Internet presence that entices prospective patients to contact or visit our physical store.

Target Market(s)

Patients Medicos and Veterinary clients

Industry/Entity Type

Pharmacy

Coding

Coded - Design and coding required

Number of Pages Required

1 page

Requirements
Must have
• Clear friendly image
Nice to have
• soft enticing feel
Should not have
• No crass loud unprofessional elements

```html
<!DOCTYPE html>
<html lang="en">
<head>
<meta charset="utf-8">
<title>Willowbank Compounding Pharmacy</title>
<link href="https://fonts.googleapis.com/css2?family=Open+Sans:wght@300;400;600;700&display=swap" rel="stylesheet">
<style>
:root{
  --blue:#1e8fd6;
  --blue-dark:#1672b0;
  --blue-light:#5bb4ea;
  --orange:#f28c28;
  --text:#555;
  --heading:#4a4a4a;
  --rule:#e3e3e3;
  --footer-bg:#f4f4f4;
  --bar:#dedede;
}
*{box-sizing:border-box;margin:0;padding:0}
html,body{width:861px;height:1200px;overflow:hidden;background:#fff}
body{font-family:"Open Sans",Arial,sans-serif;color:var(--text);position:relative}
.header{height:80px;display:flex;align-items:center;padding:0 130px;gap:28px}
.brand{display:flex;align-items:center;gap:8px;width:200px}
.brand-mark{width:20px;height:20px;background:var(--blue);border-radius:50%}
.brand-name{font-size:14px;font-weight:700;color:var(--blue);line-height:1.1}
.header-info{font-size:8px;line-height:1.45;color:#666}
.header-info strong{color:#444}
.header-contact{margin-left:auto;font-size:8px;line-height:1.6;color:#666}
.header-contact span{color:var(--blue)}
.nav{height:26px;background:var(--blue);display:flex;align-items:center;padding-left:165px;gap:54px}
.nav a{color:#fff;font-size:10px;font-weight:600;text-decoration:none;letter-spacing:.3px}
.hero{position:relative;height:444px;background:linear-gradient(100deg,#e9eef2 0%,#cfdde8 35%,#b8cfdf 60%,#dce6ec 100%)}
.hero-copy{position:absolute;left:0;right:0;top:218px;text-align:center}
.hero-title{font-size:38px;font-weight:300;color:#fff;letter-spacing:1px;text-shadow:0 1px 3px rgba(0,0,0,.35)}
.hero-band{display:inline-block;margin-top:8px;background:rgba(30,143,214,.88);padding:8px 46px;color:#fff}
.hero-band .is{display:block;font-size:17px;font-weight:300}
.hero-band .tag{display:block;font-size:18px;font-weight:400;letter-spacing:.5px}
.dots{position:absolute;bottom:16px;left:0;right:0;display:flex;justify-content:center;gap:6px}
.dots i{width:7px;height:7px;border-radius:50%;background:rgba(255,255,255,.7)}
.dots i.on{background:var(--blue)}
.about{width:600px;margin:22px auto 0}
.about h1{font-size:20px;font-weight:400;color:var(--heading);text-align:center;letter-spacing:.5px;margin-bottom:12px}
.about p{font-size:8.5px;line-height:1.65;margin-bottom:8px;text-align:justify}
.featured{width:600px;margin:6px auto 0}
.featured h2{text-align:center;font-size:15px;font-weight:400;color:var(--heading);letter-spacing:1px;margin-bottom:16px}
.cards{display:flex;gap:15px}
.card{flex:1}
.card-photo{height:98px}
.card-body{height:78px;padding:8px 10px;color:#fff;text-align:center}
.card-body h3{font-size:12px;font-weight:600;margin-bottom:4px}
.card-body p{font-size:7.5px;line-height:1.5}
.blue{background:var(--blue)}
.orange{background:var(--orange)}
.footer{position:absolute;left:0;right:0;top:1072px;height:103px;background:var(--footer-bg);display:flex;padding:14px 130px 0;gap:40px}
.footer h4{font-size:12px;font-weight:400;color:var(--heading);margin-bottom:6px;border-bottom:1px solid var(--rule);padding-bottom:3px}
.footer p{font-size:8px;line-height:1.6}
.col-hours{width:150px}
.col-map{width:190px}
.map{height:58px;background:linear-gradient(135deg,#e8ece4,#d6dfd2)}
.social{display:flex;gap:5px;margin-top:6px}
.social i{width:13px;height:13px;border-radius:50%;background:var(--blue)}
.copyright{position:absolute;left:0;right:0;bottom:0;height:25px;background:var(--bar);font-size:7.5px;color:#777;padding:8px 130px}
</style>
</head>
<body>
<header class="header">
  <div class="brand"><span class="brand-mark"></span><span class="brand-name">Willowbank<br>Compounding Pharmacy</span></div>
  <div class="header-info"><strong>WILLOWBANK PHARMACY</strong><br>Shop 4, 12 Market Street<br>Riverside NSW 2000<br>Open 7 days</div>
  <div class="header-contact">Phone: <span>(02) 5550 1842</span><br>Fax: <span>(02) 5550 1843</span><br>Email: <span>care@willowbankpharmacy.example</span></div>
</header>
<nav class="nav"><a>HOME</a><a>ABOUT US</a><a>LOCATIONS</a><a>TIMINGS</a><a>CONTACT US</a></nav>
<section class="hero">
  <div role="img" aria-label="Two smiling pharmacists in white coats standing in a pharmacy aisle" style="position:absolute;inset:0"></div>
  <div class="hero-copy">
    <div class="hero-title">COMPOUNDING PHARMACY</div>
    <div class="hero-band"><span class="is">IS</span><span class="tag">CUSTOMISED MEDICATIONS FOR PATIENTS.</span></div>
  </div>
  <div class="dots"><i class="on"></i><i></i><i></i></div>
</section>
<section class="about">
  <h1>WHAT IS COMPOUNDING PHARMACY?</h1>
  <p>Compounding is the art of preparing personalised medicines for patients. Our pharmacists work closely with doctors and vets to create dosage forms that suit each person, from creams and capsules to flavoured liquids, when a standard product is not available or not suitable.</p>
  <p>In our purpose built laboratory we combine traditional skills with modern equipment and quality ingredients. Every preparation is made to order, checked carefully and labelled clearly, so you can feel confident in the medicine you receive and the care behind it.</p>
  <p>Compounding can help when a patient needs a different strength, cannot swallow tablets, is allergic to a filler or dye, or when a product has been discontinued. We also prepare medicines for animals in forms and flavours that make dosing easier.</p>
  <p>Ask our friendly team how compounding could help you, your family or your pets. Visit us in store or contact us today to talk with a pharmacist.</p>
</section>
<section class="featured">
  <h2>FEATURED ITEMS</h2>
  <div class="cards">
    <article class="card">
      <div class="card-photo" role="img" aria-label="A dog and cat resting together" style="background:linear-gradient(135deg,#d9c7a8,#b8a07c)"></div>
      <div class="card-body blue"><h3>Vet Articles</h3><p>Gentle, easy to give medicines for pets, made in the strength and flavour your vet recommends for cats, dogs and horses.</p></div>
    </article>
    <article class="card">
      <div class="card-photo" role="img" aria-label="Sunlit beach with a parasol" style="background:linear-gradient(135deg,#f4d79a,#e9a85c)"></div>
      <div class="card-body orange"><h3>Sun Therapy</h3><p>Soothing creams and balms prepared to suit sensitive skin, free from harsh additives and made fresh in our laboratory.</p></div>
    </article>
    <article class="card">
      <div class="card-photo" role="img" aria-label="Doctor examining a patient's neck" style="background:linear-gradient(135deg,#e8d6c6,#c9b3a0)"></div>
      <div class="card-body blue"><h3>Thyroid Extract</h3><p>Carefully prepared capsules in precise strengths, made to your doctor's prescription and checked by our experienced pharmacists.</p></div>
    </article>
  </div>
</section>
<footer class="footer">
  <div class="col-hours"><h4>Working Hours</h4><p>7 days a week<br>8.30 am to 6.30 pm</p></div>
  <div class="col-map"><h4>Our Map</h4><div class="map" role="img" aria-label="Street map showing the pharmacy location"></div></div>
  <div class="col-contact"><h4>Contact Info</h4><p>Phone: (02) 5550 1842<br>Fax: (02) 5550 1843<br>Email: care@willowbankpharmacy.example</p><div class="social"><i></i><i></i><i></i><i></i></div></div>
</footer>
<div class="copyright">© 2024 Willowbank Pharmacy. All rights reserved.</div>
</body>
</html>
```